New bussiness card, using company logo.
Lionel Brisk
Manager/Director
Brisk Property Developments
Po Box 5347
Thuringowa Central
Qld
0491 638 205
lionel@briskpropertydevelopments
eye catching, vibrant colours, professional

```html
<!DOCTYPE html>
<html lang="en">
<head>
<meta charset="utf-8">
<title>Brisk Property Developments – Business Cards</title>
<link rel="stylesheet" href="https://fonts.googleapis.com/css2?family=Open+Sans:wght@400;600;700&display=swap">
<style>
  :root {
    --backdrop: #2b2724;
    --card-white: #ffffff;
    --brand-red: #e0252d;
    --brand-green: #7cc142;
    --green-light: #92c83e;
    --green-deep: #5db546;
    --ink: #1e1e1e;
    --ink-soft: #6b6b6b;
    --rule: #c9c9c9;
  }
  * { box-sizing: border-box; margin: 0; padding: 0; }
  html, body {
    width: 1200px; height: 721px; overflow: hidden;
    background: var(--backdrop);
    font-family: "Open Sans", Arial, sans-serif;
  }
  .sheet { position: relative; width: 1200px; height: 721px; }

  .card { position: absolute; overflow: hidden; }
  .card--front   { left: 41px;  top: 37px;  width: 548px; height: 311px; background: var(--card-white); }
  .card--brand   { left: 614px; top: 37px;  width: 547px; height: 311px; background: var(--card-white); }
  .card--red     { left: 41px;  top: 376px; width: 548px; height: 310px; background: var(--brand-red); }
  .card--green   { left: 614px; top: 378px; width: 547px; height: 312px;
                   background: linear-gradient(120deg, var(--green-light), var(--green-deep)); }

  .wordmark {
    position: absolute; font-weight: 700; white-space: nowrap;
    text-align: center; letter-spacing: 0.2px;
  }
  .card--front .wordmark { left: 44px; top: 134px; width: 260px; font-size: 17px; color: var(--brand-red); }
  .card--brand .wordmark { left: 0; top: 152px; width: 100%; font-size: 24px; color: var(--brand-red); }
  .card--red .wordmark   { left: 0; top: 152px; width: 100%; font-size: 25px; color: var(--card-white); }
  .card--green .wordmark { left: 0; top: 155px; width: 100%; font-size: 25px; color: var(--card-white); }

  .divider { position: absolute; left: 325px; top: 59px; width: 1px; height: 135px; background: var(--rule); }

  .contact { position: absolute; left: 347px; top: 65px; color: var(--ink); font-size: 13.5px; line-height: 19px; }
  .contact__name { color: var(--brand-red); font-size: 18.5px; font-weight: 700; line-height: 24px; }
  .contact__role { color: var(--ink-soft); font-size: 14.5px; line-height: 18px; }
  .contact__phone { margin-top: 19px; display: flex; align-items: center; gap: 6px; }
  .contact__address { margin-top: 9px; }

  .icon { width: 11px; height: 11px; flex: none; }

  .stripe { position: absolute; top: 259px; height: 11px; }
  .stripe--red   { left: 0; width: 323px; background: var(--brand-red); }
  .stripe--green { left: 328px; right: 0; background: var(--brand-green); }

  .email {
    position: absolute; left: 0; width: 100%; top: 281px;
    display: flex; justify-content: center; align-items: center; gap: 7px;
    font-size: 15px; color: var(--ink); letter-spacing: 0.6px;
  }

  .web {
    position: absolute; left: 0; width: 100%; text-align: center;
    font-size: 15.5px; letter-spacing: 1.4px;
  }
  .card--brand .web { top: 269px; color: var(--ink); }
  .card--red .web   { top: 270px; color: var(--card-white); }
  .card--green .web { top: 269px; color: var(--card-white); }
</style>
</head>
<body>
<main class="sheet">

  <section class="card card--front">
    <div class="wordmark">Brisk Property Developments</div>
    <div class="divider"></div>
    <div class="contact">
      <div class="contact__name">Lionel Brisk</div>
      <div class="contact__role">Manager/Director</div>
      <div class="contact__phone">
        <svg class="icon" viewBox="0 0 12 12" aria-hidden="true">
          <circle cx="6" cy="6" r="5.3" fill="none" stroke="#7cc142" stroke-width="1.2"/>
          <path d="M4 3.2 L5.2 3.2 L5.6 4.8 L4.9 5.4 Q5.7 6.9 7 7.4 L7.6 6.7 L9 7.2 L9 8.3 Q6.5 9 4.6 6.8 Q3.4 5 4 3.2 Z" fill="#7cc142"/>
        </svg>
        <span>0491 638 205</span>
      </div>
      <div class="contact__address">Po Box 5347<br>Wattlebrook Central , Wbk</div>
    </div>
    <div class="stripe stripe--red"></div>
    <div class="stripe stripe--green"></div>
    <div class="email">
      <svg class="icon" viewBox="0 0 12 12" aria-hidden="true">
        <rect x="1" y="3" width="10" height="7" fill="#7cc142"/>
        <path d="M1 3 L6 7 L11 3" fill="none" stroke="#fff" stroke-width="1"/>
      </svg>
      <span>lionel@briskpropertydevelopments.com</span>
    </div>
  </section>

  <section class="card card--brand">
    <div class="wordmark">Brisk Property Developments</div>
    <div class="web">www.briskpropertydevelopments.com</div>
  </section>

  <section class="card card--red">
    <div class="wordmark">Brisk Property Developments</div>
    <div class="web">www.briskpropertydevelopments.com</div>
  </section>

  <section class="card card--green">
    <div class="wordmark">Brisk Property Developments</div>
    <div class="web">www.briskpropertydevelopments.com</div>
  </section>

</main>
</body>
</html>
```